New Innovative Counselling and psychotherapy Service needs Business Card design

Keep it simple and professional. On one side, just company name and logo (perhaps in all blue) and maybe a tag line.

On other side (all white) my name and Qualifications in centre

Industry/Entity Type

Health And Wellness

Contact Information for Business Card

Dara Whelby
Counsellor & Psychotherapist
BSc (Psychol.), BA, Dip. (Couns. & Psych.), PG.Cert (CBT), FGTrK, ONRE

I will also require Mobile no, Email and web site address of which I'll pass on to final designer.

Font styles to use
Sans Serif

Requirements
Must have
• My Logo Only and please use the colours in logo that is in it.
Should not have
• Any other images

```html
<!DOCTYPE html>
<html lang="en">
<head>
<meta charset="utf-8">
<title>Brightwell Lane – Business Card</title>
<link href="https://fonts.googleapis.com/css2?family=Roboto:wght@300;400;500;700&display=swap" rel="stylesheet">
<style>
  :root {
    --sky: #4fb6ea;
    --sky-deep: #3f9fd6;
    --leaf: #8cc653;
    --ink: #333638;
    --ink-soft: #4a4d50;
    --paper: #ffffff;
    --backdrop: #e4e5e6;
  }
  * { margin: 0; padding: 0; box-sizing: border-box; }
  html, body {
    width: 1200px; height: 726px; overflow: hidden;
    background: var(--backdrop);
    font-family: "Roboto", Arial, sans-serif;
  }
  .sheet {
    position: relative; width: 1200px; height: 726px;
    display: flex; align-items: center; justify-content: center; gap: 40px;
  }
  .card {
    position: relative; width: 540px; height: 309px; overflow: hidden;
    box-shadow: 0 6px 18px rgba(0,0,0,0.12);
  }
  /* Front */
  .card-front {
    background: var(--sky);
    display: flex; flex-direction: column; align-items: center; justify-content: center;
  }
  .brand { display: flex; align-items: center; gap: 16px; }
  .brand-dot { width: 58px; height: 58px; border-radius: 50%; flex: none; }
  .brand-name { font-weight: 300; line-height: 1; white-space: nowrap; }
  .card-front .brand-dot { background: var(--paper); }
  .card-front .brand-name { color: var(--paper); font-size: 40px; }
  .tagline-front {
    margin-top: 10px; margin-left: 74px;
    color: var(--paper); font-size: 15px; letter-spacing: 0.42em; font-weight: 400;
  }
  /* Back */
  .card-back { background: var(--paper); }
  .card-back .brand { position: absolute; left: 34px; top: 64px; }
  .card-back .brand-dot { background: var(--sky-deep); width: 62px; height: 62px; }
  .card-back .brand-name { color: var(--ink); font-size: 38px; }
  .contact {
    position: absolute; right: 30px; top: 150px;
    list-style: none; font-size: 13px; color: var(--ink);
  }
  .contact li { display: flex; align-items: center; gap: 8px; height: 20px; }
  .contact svg { width: 12px; height: 12px; flex: none; }
  .person { position: absolute; left: 34px; top: 206px; }
  .person-name { color: var(--sky-deep); font-weight: 700; font-size: 22px; margin-bottom: 4px; }
  .person-role, .person-quals { color: var(--ink-soft); font-size: 12.5px; line-height: 15px; }
  .person-quals { width: 270px; }
  .band-green {
    position: absolute; left: 0; right: 0; bottom: 0; height: 10px; background: var(--leaf);
  }
  .band-tab {
    position: absolute; right: 0; bottom: 0; width: 232px; height: 52px;
    background: var(--sky); border-top-left-radius: 12px;
    color: var(--paper); font-size: 13px;
    display: flex; align-items: center; justify-content: center;
  }
</style>
</head>
<body>
<main class="sheet">
  <section class="card card-front" aria-label="Card front">
    <div class="brand">
      <span class="brand-dot"></span>
      <span class="brand-name">Brightwell Lane</span>
    </div>
    <p class="tagline-front">A tag line goes here</p>
  </section>

  <section class="card card-back" aria-label="Card back">
    <div class="brand">
      <span class="brand-dot"></span>
      <span class="brand-name">Brightwell Lane</span>
    </div>

    <ul class="contact">
      <li>
        <svg viewBox="0 0 12 12" aria-hidden="true"><path d="M1 3c0-1 1-2 2.5-2h5C10 1 11 2 11 3v1H8.5V3h-5v1H1z M2 5h8l1 6H1z" fill="#3fae9b"/></svg>
        0961 482 3057
      </li>
      <li>
        <svg viewBox="0 0 12 12" aria-hidden="true"><rect x="0.5" y="2.5" width="11" height="7" fill="none" stroke="#3fae9b"/><path d="M0.5 2.5 6 7l5.5-4.5" fill="none" stroke="#3fae9b"/></svg>
        dara.w@BrightwellLane.com
      </li>
      <li>
        <svg viewBox="0 0 12 12" aria-hidden="true"><circle cx="6" cy="6" r="5" fill="#3fae9b"/><path d="M1 6h10M6 1c-2 2.5-2 7.5 0 10M6 1c2 2.5 2 7.5 0 10" stroke="#fff" stroke-width="0.7" fill="none"/></svg>
        www.BrightwellLane.com
      </li>
    </ul>

    <div class="person">
      <h1 class="person-name">Dara Whelby</h1>
      <p class="person-role">Counsellor &amp; Psychotherapist</p>
      <p class="person-quals">BSc (Psychol.), BA, Dip. (Couns. &amp; Psych.), PG.Cert (CBT), FGTrK, ONRE</p>
    </div>

    <div class="band-green"></div>
    <div class="band-tab">A tag line goes here</div>
  </section>
</main>
</body>
</html>
```